Driver License Monitoring Application Marketing Website

We need a new web design for our web application. The product is called "RoadPermitGuard." We provide a driver license monitoring service to companies and local government bodies with driver fleets. Our current website is available at www.RoadPermitGuard-example.com.

I prefer a clean, single-page design with good SEO. Attached are some PDFs with data about the project.

Target Market(s)

Companies with driver fleets, local government.

Industry/Entity Type

Government

Coding

Coded - Design and coding required

Number of Pages Required

1 page

Colors
000000

Requirements
Must have
• Content from current www.RoadPermitGuard-example.com and attached PDFs.
Nice to have
• Prefer a simple Bootstrap or similar design for easy editing.
• Room for a simple video explanation of how the product works (we don't have an actual video yet)

```html
<!DOCTYPE html>
<html lang="en">
<head>
<meta charset="utf-8">
<title>RoadPermitGuard – Florida Driver License Monitoring</title>
<link rel="stylesheet" href="https://fonts.googleapis.com/css2?family=Source+Sans+Pro:wght@300;400;600;700&family=Playfair+Display:ital@1&family=Tinos&family=Montserrat:wght@500;700&display=swap">
<style>
  :root{
    --red:#b41d23;
    --red-bright:#c8202a;
    --ink:#333d47;
    --body:#6b6f74;
    --link:#2ba6de;
    --white:#ffffff;
    --footer:#141416;
    --footer-deep:#0d0d0e;
    --line:#d9d9d9;
  }
  *{box-sizing:border-box;margin:0;padding:0}
  html,body{width:1200px;height:2410px;overflow:hidden;background:var(--white)}
  body{position:relative;font-family:"Source Sans Pro",Arial,sans-serif;color:var(--body)}

  .hero{position:absolute;left:0;top:0;width:1200px;height:852px;overflow:hidden}
  .hero-photo{position:absolute;inset:0;
    background:
      radial-gradient(ellipse 520px 300px at 260px 470px, rgba(170,30,30,.55), transparent 70%),
      radial-gradient(ellipse 90px 110px at 1045px 470px, rgba(170,30,30,.5), transparent 70%),
      linear-gradient(180deg,#2f5687 0%,#4b77a8 28%,#8aa9c8 48%,#6a6e72 62%,#3d3f42 100%)}
  .hero-shade{position:absolute;inset:0;background:rgba(10,14,22,.32)}
  .nav{position:absolute;left:0;top:0;width:1200px;height:110px}
  .brand{position:absolute;left:100px;top:40px;font-family:"Tinos",serif;font-size:24px;color:var(--white);letter-spacing:.5px}
  .menu{position:absolute;top:46px;left:496px;display:flex;gap:0;font-family:"Montserrat",sans-serif;font-size:13px;font-weight:500;letter-spacing:1.4px;color:var(--white)}
  .menu span{margin-right:40px}
  .search{position:absolute;left:1077px;top:41px;width:27px;height:27px}
  .slide-arrow{position:absolute;top:408px;width:24px;height:38px}
  .slide-arrow.prev{left:32px}
  .slide-arrow.next{left:1142px}
  .hero-copy{position:absolute;left:0;top:0;width:1200px;text-align:center;color:var(--white)}
  .hero-rule{position:absolute;left:577px;top:245px;width:46px;height:2px;background:var(--red-bright)}
  .hero-kicker{position:absolute;left:0;width:1200px;top:265px;font-family:"Playfair Display",serif;font-style:italic;font-size:17px}
  .hero-title{position:absolute;left:0;width:1200px;top:306px;font-weight:300;font-size:70px;line-height:86px}
  .hero-lead{position:absolute;left:0;width:1200px;top:518px;font-family:"Tinos",serif;font-size:25px;line-height:34px}
  .hero-btn{position:absolute;left:502px;top:663px;width:189px;height:35px;border-radius:18px;background:var(--red);font-family:"Montserrat",sans-serif;font-weight:700;font-size:11px;letter-spacing:1.6px;line-height:35px;text-align:center}

  .intro{position:absolute;left:0;top:852px;width:1200px;text-align:center}
  .intro h2{position:absolute;left:0;width:1200px;top:50px;font-weight:700;font-size:35px;color:var(--ink);letter-spacing:-.5px}
  .intro-rule{position:absolute;left:524px;top:104px;width:152px;height:1px;background:var(--line)}
  .intro p{position:absolute;left:95px;width:1010px;top:147px;font-size:16.5px;line-height:25px;color:var(--body)}
  .product-shot{position:absolute;left:362px;top:259px;width:474px;height:388px;border-radius:6px;
    background:linear-gradient(180deg,#2b3033 0%,#2b3033 6%,#e9ecee 6%,#f6f7f8 58%,#dcdde0 62%,#ffffff 68%,#eceeef 100%)}

  .features{position:absolute;left:0;top:1572px;width:1200px}
  .feature{position:absolute;width:300px;text-align:center}
  .feature .icon{display:block;margin:0 auto;width:98px;height:98px}
  .feature h3{margin-top:30px;font-family:"Montserrat",sans-serif;font-weight:500;font-size:14px;letter-spacing:2px;color:var(--ink)}
  .feature p{margin:20px auto 0;width:262px;font-size:15.5px;line-height:26px;color:var(--body)}
  .feature .more{display:inline-flex;align-items:center;gap:5px;margin-top:40px;font-size:12px;color:var(--link)}

  .cta{position:absolute;left:0;top:2015px;width:1200px;height:167px;background:var(--red)}
  .cta-text{position:absolute;left:140px;width:530px;top:44px;text-align:center;font-size:25px;font-weight:300;letter-spacing:1.5px;line-height:36px;color:var(--white)}
  .cta-btn{position:absolute;left:782px;top:56px;width:220px;height:52px;border:2px solid var(--white);font-family:"Montserrat",sans-serif;font-weight:700;font-size:12px;letter-spacing:1.4px;line-height:48px;text-align:center;color:var(--white)}

  .footer{position:absolute;left:0;top:2182px;width:1200px;height:151px;background:var(--footer)}
  .footer-brand{position:absolute;left:100px;top:47px;font-family:"Tinos",serif;font-size:26px;color:var(--white);letter-spacing:.5px}
  .footer-tag{position:absolute;left:100px;top:82px;font-size:13px;color:#c9c9c9}
  .social{position:absolute;left:882px;top:66px;display:flex;gap:18px}
  .social span{width:18px;height:18px;border-radius:50%;background:var(--white)}
  .legal{position:absolute;left:0;top:2333px;width:1200px;height:77px;background:var(--footer-deep)}
  .legal-copy{position:absolute;left:100px;top:35px;font-size:11px;color:#4b4c4f}
  .legal-brand{position:absolute;left:998px;top:35px;font-family:"Tinos",serif;font-size:10px;color:#cfcfcf}
</style>
</head>
<body>

<header class="hero">
  <div class="hero-photo" role="img" aria-label="Photo of a red semi-truck driving on an open highway under a blue sky, with a second truck in the distance"></div>
  <div class="hero-shade"></div>

  <nav class="nav">
    <div class="brand">RoadPermitGuard</div>
    <div class="menu"><span>HOME</span><span>LICENSE MONITORING</span><span>ABOUT</span><span>CONTACT</span><span>LOGIN</span></div>
    <svg class="search" viewBox="0 0 27 27" aria-label="Search">
      <circle cx="13.5" cy="13.5" r="12.5" fill="none" stroke="#fff" stroke-width="1.6"/>
      <circle cx="12.3" cy="12.3" r="3.6" fill="none" stroke="#fff" stroke-width="1.6"/>
      <line x1="15" y1="15" x2="18" y2="18" stroke="#fff" stroke-width="1.8" stroke-linecap="round"/>
    </svg>
  </nav>

  <svg class="slide-arrow prev" viewBox="0 0 24 38" aria-label="Previous slide"><polyline points="20,2 4,19 20,36" fill="none" stroke="rgba(255,255,255,.6)" stroke-width="2"/></svg>
  <svg class="slide-arrow next" viewBox="0 0 24 38" aria-label="Next slide"><polyline points="4,2 20,19 4,36" fill="none" stroke="rgba(255,255,255,.6)" stroke-width="2"/></svg>

  <div class="hero-copy">
    <div class="hero-rule"></div>
    <div class="hero-kicker">Monitor your fleet electronically</div>
    <h1 class="hero-title">Florida Driver<br>License Monitoring</h1>
    <p class="hero-lead">Get alerts by Email and Online.<br>Never let another unlicensed or unauthorized driver behind the wheel.</p>
    <div class="hero-btn">MORE INFORMATION</div>
  </div>
</header>

<section class="intro">
  <h2>Monitor your drivers electronically, twenty-four hours a day.</h2>
  <div class="intro-rule"></div>
  <p>How many of your drivers currently have a suspended license? The answer may surprise you. Driving with a suspended license is the most commonly committed offense in America. In 2011, over 1.8 million licenses got suspended in Florida. With just over 15 million drivers, that's 12% of all licensed Florida drivers.</p>
  <div class="product-shot" role="img" aria-label="Desktop computer with keyboard, mouse and coffee mug, showing the license monitoring dashboard summary screen"></div>
</section>

<section class="features">
  <div class="feature" style="left:117px">
    <svg class="icon" viewBox="0 0 98 98" aria-hidden="true">
      <circle cx="49" cy="49" r="48" fill="#fff" stroke="#e3e3e3"/>
      <rect x="34" y="36" width="30" height="21" rx="2" fill="#3a4047"/>
      <rect x="37" y="39" width="24" height="15" fill="#fff"/>
      <rect x="45" y="57" width="8" height="5" fill="#3a4047"/>
      <rect x="40" y="61" width="18" height="3" rx="1" fill="#3a4047"/>
    </svg>
    <h3>LICENSE MONITORING</h3>
    <p>Monitor your fleet electronically. Get alerts by email and online. Never let another unlicensed or unauthorized driver behind the wheel.</p>
    <span class="more">Understand more <svg width="14" height="14" viewBox="0 0 14 14"><circle cx="7" cy="7" r="6" fill="none" stroke="#2ba6de"/><polyline points="6,4.5 8.5,7 6,9.5" fill="none" stroke="#2ba6de" stroke-width="1.3"/></svg></span>
  </div>

  <div class="feature" style="left:450px">
    <svg class="icon" viewBox="0 0 98 98" aria-hidden="true">
      <circle cx="49" cy="49" r="48" fill="#fff" stroke="#e3e3e3"/>
      <path d="M37 48 L41 38 H57 L61 48 Z" fill="#3a4047"/>
      <rect x="33" y="47" width="32" height="12" rx="3" fill="#3a4047"/>
      <rect x="35" y="58" width="6" height="5" rx="1" fill="#3a4047"/>
      <rect x="57" y="58" width="6" height="5" rx="1" fill="#3a4047"/>
      <circle cx="39" cy="53" r="2.3" fill="#fff"/>
      <circle cx="59" cy="53" r="2.3" fill="#fff"/>
      <path d="M43 46 L45 41 H53 L55 46 Z" fill="#fff"/>
    </svg>
    <h3>PRIVATE SECTOR</h3>
    <p>Monitor your fleet electronically. Get alerts by email and online. Never let another unlicensed or unauthorized driver behind the wheel.</p>
    <span class="more">Understand more <svg width="14" height="14" viewBox="0 0 14 14"><circle cx="7" cy="7" r="6" fill="none" stroke="#2ba6de"/><polyline points="6,4.5 8.5,7 6,9.5" fill="none" stroke="#2ba6de" stroke-width="1.3"/></svg></span>
  </div>

  <div class="feature" style="left:782px">
    <svg class="icon" viewBox="0 0 98 98" aria-hidden="true">
      <circle cx="49" cy="49" r="48" fill="#fff" stroke="#e3e3e3"/>
      <polygon points="49,33 65,41 33,41" fill="#3a4047"/>
      <rect x="34" y="42" width="30" height="3" fill="#3a4047"/>
      <rect x="37" y="46" width="4" height="13" fill="#3a4047"/>
      <rect x="44" y="46" width="4" height="13" fill="#3a4047"/>
      <rect x="51" y="46" width="4" height="13" fill="#3a4047"/>
      <rect x="58" y="46" width="4" height="13" fill="#3a4047"/>
      <rect x="33" y="60" width="32" height="4" fill="#3a4047"/>
    </svg>
    <h3>PUBLIC SECTOR</h3>
    <p>Monitor your fleet electronically. Get alerts by email and online. Never let another unlicensed or unauthorized driver behind the wheel.</p>
    <span class="more">Understand more <svg width="14" height="14" viewBox="0 0 14 14"><circle cx="7" cy="7" r="6" fill="none" stroke="#2ba6de"/><polyline points="6,4.5 8.5,7 6,9.5" fill="none" stroke="#2ba6de" stroke-width="1.3"/></svg></span>
  </div>
</section>

<section class="cta">
  <div class="cta-text">MONITOR YOUR DRIVERS ELECTRONICALLY,<br>TWENTY-FOUR HOURS A DAY.</div>
  <div class="cta-btn">TRACK YOUR FLEET</div>
</section>

<footer class="footer">
  <div class="footer-brand">RoadPermitGuard</div>
  <div class="footer-tag">Created by experts in Florida traffic law.</div>
  <div class="social" aria-label="Social links"><span></span><span></span><span></span><span></span><span></span></div>
</footer>
<div class="legal">
  <div class="legal-copy">© 2015 RoadPermitGuard. All Rights Reserved.</div>
  <div class="legal-brand">RoadPermitGuard</div>
</div>

</body>
</html>
```